wealth management firm, professional group, new model

we have a logo that works but we need a card, white background using our colors...clean look

our tag line if can be used in

The Path From Saver to Steward

```html
<!DOCTYPE html>
<html lang="en">
<head>
<meta charset="utf-8">
<title>Carrow Wealth Partners – Business Card</title>
<link href="https://fonts.googleapis.com/css2?family=Montserrat:wght@400;500&family=Poppins:wght@400;500;600&family=Mrs+Saint+Delafield&display=swap" rel="stylesheet">
<style>
  :root {
    --backdrop: #bdbec0;
    --card: #ffffff;
    --navy: #14254a;
    --navy-soft: #1d2d4f;
    --grey-text: #7a7a7a;
    --grey-script: #8c8c8c;
    --divider: #b5b9c2;
  }
  * { margin: 0; padding: 0; box-sizing: border-box; }
  html, body { width: 1200px; height: 1000px; overflow: hidden; }
  body {
    background: var(--backdrop);
    position: relative;
    font-family: "Montserrat", sans-serif;
  }
  .card {
    position: absolute;
    left: 281px;
    width: 639px;
    height: 357px;
    background: var(--card);
    border-radius: 20px;
  }
  .card--front { top: 81px; }
  .card--back { top: 536px; }

  .brand { position: absolute; left: 0; width: 100%; text-align: center; color: var(--navy); font-family: "Montserrat", sans-serif; font-weight: 400; }
  .brand__name { display: block; text-transform: uppercase; }
  .brand__sub { display: block; text-transform: uppercase; }

  .card--front .brand { top: 160px; }
  .card--front .brand__name { font-size: 50px; letter-spacing: 22px; padding-left: 22px; line-height: 60px; }
  .card--front .brand__sub { font-size: 20px; letter-spacing: 2.4px; margin-top: 22px; }

  .tagline {
    position: absolute;
    top: 280px; left: 0; width: 100%;
    text-align: center;
    font-family: "Mrs Saint Delafield", cursive;
    font-size: 46px;
    letter-spacing: 1px;
    color: var(--grey-script);
    white-space: nowrap;
  }

  .card--back .brand { top: 80px; }
  .card--back .brand__name { font-size: 24px; letter-spacing: 9px; padding-left: 9px; line-height: 32px; }
  .card--back .brand__sub { font-size: 10.5px; letter-spacing: 1.2px; margin-top: 9px; }

  .person {
    position: absolute;
    right: 337px; top: 196px;
    text-align: right;
    font-family: "Poppins", sans-serif;
  }
  .person__name { font-size: 23px; font-weight: 600; color: var(--navy-soft); line-height: 28px; }
  .person__title { font-size: 14px; letter-spacing: 2.5px; color: var(--navy-soft); line-height: 18px; }

  .divider { position: absolute; left: 316px; top: 199px; width: 1px; height: 42px; background: var(--divider); }

  .contact { position: absolute; left: 333px; top: 197px; font-family: "Poppins", sans-serif; font-size: 17px; color: var(--grey-text); list-style: none; }
  .contact li { display: flex; align-items: center; height: 21px; }
  .contact svg { width: 18px; height: 14px; margin-right: 9px; fill: var(--navy-soft); }

  .website {
    position: absolute; top: 316px; left: 0; width: 100%;
    text-align: center;
    font-family: "Poppins", sans-serif;
    font-size: 17px;
    color: #9a9a9a;
  }
  .website strong { font-weight: 600; color: #8a8a8a; }
</style>
</head>
<body>
  <section class="card card--front">
    <div class="brand">
      <span class="brand__name">Carrow</span>
      <span class="brand__sub">Wealth Partners</span>
    </div>
    <p class="tagline">The Path From Saver to Steward</p>
  </section>

  <section class="card card--back">
    <div class="brand">
      <span class="brand__name">Carrow</span>
      <span class="brand__sub">Wealth Partners</span>
    </div>

    <div class="person">
      <p class="person__name">Name Surname</p>
      <p class="person__title">TITLE</p>
    </div>
    <div class="divider"></div>
    <ul class="contact">
      <li>
        <svg viewBox="0 0 24 24" aria-hidden="true"><path d="M6.6 10.8c1.4 2.8 3.8 5.1 6.6 6.6l2.2-2.2c.3-.3.7-.4 1-.2 1.1.4 2.3.6 3.6.6.6 0 1 .4 1 1V20c0 .6-.4 1-1 1C10.6 21 3 13.4 3 4c0-.6.4-1 1-1h3.5c.6 0 1 .4 1 1 0 1.3.2 2.5.6 3.6.1.3 0 .7-.2 1z"/></svg>
        012 345 6789
      </li>
      <li>
        <svg viewBox="0 0 24 18" aria-hidden="true"><path d="M0 0h24v2L12 10 0 2z"/><path d="M0 4.5l8 5.3L0 16zM24 4.5v11.5l-8-6.2zM9.6 10.9L12 12.5l2.4-1.6L24 18H0z"/></svg>
        email@carrowwealth.com
      </li>
    </ul>

    <p class="website"><strong>carrowwealth</strong>.com</p>
  </section>
</body>
</html>
```